Business Card Design (NEW FILES)

ATTENTION: New vector files are available. Please update your design to reflect/use the new (better resolution) logo images.

Seeking a unique and professional business card design for a commercial drone photography/videography business. The layout should feature
the logo (attached) and include the following information:
Owen Tarrick
614-502-7738
www.skylarkreelworks.example
NRD Certified Remote Pilot

Owen Tarrick

```html
<!DOCTYPE html>
<html lang="en">
<head>
<meta charset="utf-8">
<title>Skylark Reelworks – Business Card</title>
<link rel="stylesheet" href="https://fonts.googleapis.com/css2?family=Open+Sans:wght@400;600;700;800&display=swap">
<style>
  :root {
    --stage: #232323;
    --navy: #151a47;
    --navy-soft: #1d2a78;
    --orange: #ee8b4e;
    --teal: #14b4b3;
    --white: #ffffff;
  }
  * { box-sizing: border-box; margin: 0; padding: 0; }
  html, body { width: 1200px; height: 780px; overflow: hidden; background: var(--stage); }
  body { font-family: "Open Sans", Arial, sans-serif; position: relative; }

  .card {
    position: absolute;
    width: 560px; height: 320px;
    border-radius: 20px;
    background: var(--navy);
    overflow: hidden;
    top: 230px;
  }
  .card--front { left: 25px; }
  .card--back { left: 615px; }

  .card-art { position: absolute; inset: 0; }

  .front-glow {
    position: absolute; left: 40px; top: 20px; width: 420px; height: 280px;
    border-radius: 50%;
    background: radial-gradient(ellipse at center, rgba(45,70,190,0.45), rgba(21,26,71,0) 70%);
  }

  .brand {
    position: absolute; display: flex; align-items: center; gap: 8px;
    color: var(--white); font-weight: 600; letter-spacing: 1px; text-transform: uppercase;
  }
  .brand-dot { border-radius: 50%; background: var(--white); flex: none; }
  .card--front .brand { left: 150px; top: 240px; font-size: 20px; }
  .card--front .brand-dot { width: 14px; height: 14px; }
  .card--back .brand { left: 30px; top: 50px; font-size: 26px; }
  .card--back .brand-dot { width: 18px; height: 18px; }

  .holder { position: absolute; left: 30px; top: 150px; padding-left: 14px; border-left: 6px solid var(--orange); }
  .holder-name { font-size: 28px; font-weight: 800; line-height: 1.1; color: var(--white); }
  .holder-name .first { color: var(--orange); }
  .holder-role { font-size: 14px; font-weight: 600; color: var(--white); margin-top: 2px; }

  .contact { position: absolute; left: 56px; top: 228px; list-style: none; color: var(--white); font-size: 14px; }
  .contact li { display: flex; align-items: center; gap: 10px; line-height: 24px; }
  .contact svg { width: 14px; height: 14px; flex: none; }

  .credentials {
    position: absolute; right: 24px; top: 206px; text-align: right;
    color: var(--white); font-size: 13px; font-weight: 600; line-height: 1.35;
  }
</style>
</head>
<body>

  <section class="card card--front" aria-label="Business card front">
    <div class="front-glow"></div>
    <div class="brand"><span class="brand-dot"></span>Skylark Reelworks</div>
  </section>

  <section class="card card--back" aria-label="Business card back">
    <svg class="card-art" viewBox="0 0 560 320" aria-hidden="true">
      <line class="rule" x1="106" y1="192" x2="560" y2="192" stroke="#ffffff" stroke-width="2"/>
      <polygon class="band-orange" points="340,320 380,250 560,250 560,320" fill="#ee8b4e"/>
      <polygon class="band-orange-line" points="70,302 375,302 372,306 70,306" fill="#ee8b4e"/>
      <polygon class="band-teal" points="70,306 372,306 364,320 70,320" fill="#14b4b3"/>
    </svg>

    <div class="brand"><span class="brand-dot"></span>Skylark Reelworks</div>

    <div class="holder">
      <p class="holder-name"><span class="first">Owen</span> Tarrick</p>
      <p class="holder-role">Owner</p>
    </div>

    <ul class="contact">
      <li>
        <svg viewBox="0 0 24 24" aria-hidden="true"><path fill="#ee8b4e" d="M6.6 10.8a15 15 0 0 0 6.6 6.6l2.2-2.2a1 1 0 0 1 1-.25 11.4 11.4 0 0 0 3.6.57 1 1 0 0 1 1 1V20a1 1 0 0 1-1 1A17 17 0 0 1 3 4a1 1 0 0 1 1-1h3.5a1 1 0 0 1 1 1c0 1.25.2 2.450.57 3.57a1 1 0 0 1-.25 1z"/></svg>
        614-502-7738
      </li>
      <li>
        <svg viewBox="0 0 24 24" aria-hidden="true"><circle cx="12" cy="12" r="9" fill="none" stroke="#ee8b4e" stroke-width="2"/><path d="M3 12h18M12 3c3 3 3 15 0 18M12 3c-3 3-3 15 0 18" fill="none" stroke="#ee8b4e" stroke-width="1.5"/></svg>
        www.skylarkreelworks.example
      </li>
    </ul>

    <div class="credentials">
      <p>NRD Certified Remote Pilot</p>
      <p>Fully Insured</p>
    </div>
  </section>

</body>
</html>
```